Velmora Nightclub Flyer (Updated)

Flyer for facebook, square is fine, or rectangular. Here is the text:
VELMORA
Nightclub + Lounge
presents

B2B THURSDAY
Nov 29 2018

CLUB FLOOR:
ROLF B2B GARTH
BENEDICT SALVORTE

LOUNGE:
TOBY B2B MY COUSIN
THUNDER REGGIE

Powered by KELP Acoustics
4726 8th Avenue 21+ 9pm-2am
velmorakestrel.com for VIP booth inquiries

Target Market(s)

Nightclub

Industry/Entity Type

Night Club

Font styles to use
Sans Serif

Colors

Designer to choose colors to be used in the design.

Requirements
Must have
• All the text listed, and plz keep the theme of the attached files. We want to stay consistent with the Velmora brand
Nice to have
• Try to stay with the theme from the attachments
Should not have
• Dont' stray to far from the general theme we have from the attachments

```html
<!DOCTYPE html>
<html lang="en">
<head>
<meta charset="utf-8">
<title>Velmora Nightclub + Lounge — B2B Thursday</title>
<link href="https://fonts.googleapis.com/css2?family=Cinzel:wght@500&family=Jost:wght@300;400;500&display=swap" rel="stylesheet">
<style>
  :root {
    --mat: #e6e7e8;
    --ink: #1c1b19;
    --ink-deep: #121110;
    --gold: #e4b845;
    --gold-soft: rgba(214, 160, 48, 0.55);
    --cream: #f2efe8;
  }
  html, body {
    margin: 0;
    width: 1200px;
    height: 719px;
    overflow: hidden;
    background: var(--mat);
  }
  .flyer {
    position: absolute;
    left: 60px;
    top: 49px;
    width: 1080px;
    height: 621px;
    overflow: hidden;
    background: radial-gradient(ellipse at 50% 45%, #2a2825 0%, var(--ink) 55%, var(--ink-deep) 100%);
    font-family: "Jost", sans-serif;
    color: var(--cream);
  }
  .ribbon-area {
    position: absolute;
    left: 110px;
    top: 0;
    width: 230px;
    height: 621px;
    background: radial-gradient(ellipse 50% 60% at 50% 50%, var(--gold-soft) 0%, rgba(160, 110, 30, 0.25) 55%, rgba(40, 32, 18, 0) 100%);
  }
  .medallion {
    position: absolute;
    left: 835px;
    top: 290px;
    width: 360px;
    height: 360px;
    border-radius: 50%;
    background: radial-gradient(circle at 50% 50%, #c9962e 0%, #8a6420 45%, #4a3716 75%, rgba(40, 32, 18, 0) 100%);
  }
  .brand {
    position: absolute;
    left: 0;
    width: 100%;
    text-align: center;
  }
  .brand-name {
    top: 64px;
    margin: 0;
    font-family: "Cinzel", serif;
    font-weight: 500;
    font-size: 84px;
    line-height: 1;
    letter-spacing: 2px;
    color: var(--gold);
  }
  .brand-tagline {
    top: 148px;
    font-weight: 300;
    font-size: 23px;
    letter-spacing: 5px;
    color: var(--cream);
  }
  .brand-presents {
    top: 184px;
    font-weight: 300;
    font-size: 13px;
    letter-spacing: 3px;
    color: var(--gold);
  }
  .divider {
    position: absolute;
    left: 460px;
    width: 160px;
    height: 1px;
    background: linear-gradient(90deg, rgba(242,239,232,0), var(--cream) 20%, var(--cream) 80%, rgba(242,239,232,0));
  }
  .divider::after {
    content: "";
    position: absolute;
    left: 74px;
    top: -6px;
    width: 12px;
    height: 12px;
    border: 1px solid var(--cream);
    border-radius: 50%;
    background: var(--ink);
  }
  .divider--top { top: 214px; }
  .divider--bottom { top: 476px; }
  .lineup {
    position: absolute;
    left: 0;
    top: 236px;
    width: 100%;
    text-align: center;
    font-weight: 400;
    font-size: 17px;
    line-height: 23px;
    text-transform: uppercase;
  }
  .lineup p { margin: 0 0 20px; }
  .lineup .event-date { text-transform: none; }
  .details {
    position: absolute;
    left: 0;
    top: 514px;
    width: 100%;
    text-align: center;
    color: var(--gold);
    font-weight: 400;
  }
  .details p { margin: 0; }
  .details .small { font-size: 14px; line-height: 20px; }
  .details .web { font-size: 21px; line-height: 30px; letter-spacing: 0.3px; }
</style>
</head>
<body>
<main class="flyer">
  <div class="ribbon-area" role="img" aria-label="Flowing gold ribbon swoosh"></div>
  <div class="medallion" role="img" aria-label="Gold mandala ornament"></div>

  <h1 class="brand brand-name">VELMORA</h1>
  <div class="brand brand-tagline">NIGHTCLUB + LOUNGE</div>
  <div class="brand brand-presents">presents</div>

  <div class="divider divider--top"></div>

  <section class="lineup">
    <p>B2B Thursday<br><span class="event-date">Nov 29 2018</span></p>
    <p>Club Floor:<br>Rolf B2B Garth<br>Benedict Salvorte</p>
    <p>Lounge:<br>Toby B2B My Cousin<br>Thunder Reggie</p>
  </section>

  <div class="divider divider--bottom"></div>

  <footer class="details">
    <p class="small">Powered by KELP Acoustics</p>
    <p class="small">4726 8th Avenue 21+ 9pm-2am</p>
    <p class="web">velmorakestrel.com for VIP booth inquiries</p>
  </footer>
</main>
</body>
</html>
```